Crypto currency project website revamp

Our current website is: http://www.kobaltchain.org

The new logo is also attached.

Here are some examples of the other crypto websites. Our goal is to re-make the above website to look and feel like the followings:

1) https://zyvanlabs.com/

2) https://tavo.io/

3) https://paylume.network/#/

Please submit your designs. Once we found the right design we need to interate a bit and add 3 or 4 more sections to it.

The coded website needs to be responsive

```html
<!DOCTYPE html>
<html lang="en">
<head>
<meta charset="utf-8">
<title>Veltrin Network</title>
<link href="https://fonts.googleapis.com/css2?family=Oswald:wght@500;600;700&family=Open+Sans:ital,wght@0,400;0,600;0,700;1,400&display=swap" rel="stylesheet">
<style>
:root{
  --navy:#1b1736;
  --navy-deep:#110f22;
  --band-1:#1d1935;
  --band-2:#241f40;
  --band-3:#2c2749;
  --teal:#1fb3c8;
  --teal-dark:#1597ad;
  --ink:#1d1d1d;
  --body:#666;
  --line:#ddd;
  --white:#fff;
}
*{margin:0;padding:0;box-sizing:border-box}
html,body{width:1200px;height:3913px;overflow:hidden}
body{font-family:'Open Sans',sans-serif;color:var(--ink);background:#fff;position:relative}
section,header,footer{position:absolute;left:0;width:1200px}
.abs{position:absolute}
h1,h2,h3,h4,.brand{font-family:'Oswald',sans-serif}

/* hero */
.hero{top:0;height:626px;background:radial-gradient(ellipse at 70% 30%,#2c2a55 0%,var(--navy) 55%,var(--navy-deep) 100%);color:#fff;text-align:center}
.brand{left:97px;top:34px;display:flex;align-items:center;gap:12px;font-size:28px;font-weight:600;color:#fff}
.brand .mark{width:46px;height:46px;border:4px solid #fff;border-radius:50%}
.nav{right:97px;top:50px;display:flex;gap:34px;font-family:'Oswald',sans-serif;font-size:15px;font-weight:500;letter-spacing:.3px}
.nav a{color:#fff;text-decoration:none}
.nav a.active{color:var(--teal)}
.hero h1{top:182px;width:100%;font-size:88px;line-height:1;font-weight:700;letter-spacing:1px}
.hero .sub{top:290px;width:100%;font-size:32px;line-height:1.2;font-weight:600}
.btn{display:inline-block;background:var(--teal);color:#fff;font-family:'Oswald',sans-serif;font-weight:500;border-radius:40px;text-align:center;text-decoration:none}
.hero .btn{left:480px;top:362px;width:240px;height:60px;line-height:60px;font-size:17px}
.play{left:578px;top:500px}

/* welcome */
.welcome{top:626px;height:644px;text-align:center}
.section-title{font-size:40px;line-height:1.2;font-weight:700;color:#1a1a1a;width:100%;letter-spacing:.5px}
.welcome .section-title{top:82px}
.welcome .lead{top:155px;left:210px;width:780px;font-size:14.5px;line-height:27px;color:#555}
.feature{top:248px;width:240px}
.feature .ring{width:162px;height:162px;margin:0 auto;border:6px solid #444;border-radius:50%;display:flex;align-items:center;justify-content:center}
.feature h3{margin-top:28px;font-size:21px;font-weight:600}
.feature p{margin-top:14px;font-size:13.5px;line-height:24px;color:#777}

/* value band */
.values{top:1270px;height:488px;background:var(--band-1)}
.values .photo{left:0;top:0;width:600px;height:488px;background:radial-gradient(circle at 30% 55%,#c89a3a 0%,#7a5a20 18%,#1d3550 42%,#0d1826 100%)}
.value-row{left:600px;width:600px;height:163px;padding:22px 0 0 30px;color:#fff;display:flex;gap:28px}
.value-row:nth-of-type(2){top:0;background:var(--band-1)}
.value-row:nth-of-type(3){top:163px;background:var(--band-2)}
.value-row:nth-of-type(4){top:326px;background:var(--band-3)}
.value-row h4{font-size:22px;font-weight:600;margin-top:6px}
.value-row p{font-size:14px;line-height:26px;margin-top:8px;width:400px}
.value-row .more{display:block;margin-top:10px;color:var(--teal);font-family:'Oswald',sans-serif;font-size:15px;font-weight:500;letter-spacing:.5px}

/* blog */
.blog{top:1758px;height:762px}
.blog .section-title{top:82px;text-align:center}
.post-main{left:97px;top:178px;width:438px;height:498px;border:1px solid var(--line);box-shadow:0 2px 6px rgba(0,0,0,.08)}
.post-main .img{height:237px;background:linear-gradient(135deg,#2a3340,#151a22 60%,#6b5a3c)}
.post-main h4{margin:28px 0 0 30px;font-size:23px;font-weight:600}
.meta{font-size:12.5px;color:#666;display:flex;align-items:center;gap:6px}
.meta i{display:inline-block;width:10px;height:10px;background:var(--teal);border-radius:2px}
.post-main .meta{margin:12px 0 0 30px}
.post-main p{margin:14px 30px 0;font-size:13.5px;line-height:24px;color:#666}
.read{margin:20px 0 0 30px;display:block;color:var(--teal);font-family:'Oswald',sans-serif;font-size:15px;font-weight:500}
.post-item{left:571px;width:530px;height:114px}
.post-item .thumb{position:absolute;left:0;top:0;width:136px;height:112px;border:3px solid #eee}
.post-item h4{position:absolute;left:167px;top:0;font-size:22px;font-weight:600}
.post-item .meta{position:absolute;left:167px;top:42px}
.post-item p{position:absolute;left:167px;top:68px;width:360px;font-size:13.5px;line-height:24px;color:#666}
.blog .btn{left:571px;top:630px;width:136px;height:48px;line-height:48px;font-size:15px}

/* testimonials */
.testimonials{top:2520px;height:449px;background:linear-gradient(120deg,#22b9cc,#1aa9bf 50%,#27c0d2);color:#fff}
.testimonials .section-title{top:58px;color:#fff;text-align:center}
.quote{top:180px;width:306px;height:198px;border:2px solid rgba(255,255,255,.85);text-align:center;padding:58px 26px 0}
.quote .avatar{position:absolute;left:111px;top:-42px;width:84px;height:84px;border-radius:50%;border:4px solid #fff;background:linear-gradient(#d9c2aa,#9b7d63)}
.quote p{font-size:13.5px;line-height:24px;font-style:italic}
.quote h4{margin-top:18px;font-size:19px;font-family:'Open Sans',sans-serif;font-weight:600}
.arrow{top:262px;width:40px;height:40px;border-radius:50%;background:rgba(255,255,255,.3);display:flex;align-items:center;justify-content:center}

/* partners */
.partners{top:2969px;height:402px}
.partners .section-title{top:82px;text-align:center}
.badge{top:193px;height:92px;border:2px solid #e3e3e3;background:#fff;display:flex;align-items:center;justify-content:center}
.badge span{display:block;width:60%;height:26px;background:#c9c9c9;border-radius:4px}
.badge.feature-badge{top:180px;height:118px;box-shadow:0 2px 10px rgba(0,0,0,.15)}
.badge.feature-badge span{background:#8fb8c0}

/* footer */
.footer{top:3371px;height:542px;background:radial-gradient(ellipse at 60% 30%,#202028,#0b0b0e 70%);color:#fff}
.to-top{left:560px;top:40px;width:80px;text-align:center;font-family:'Oswald',sans-serif;font-size:14px}
.footer h3{font-size:27px;font-weight:600;letter-spacing:.3px}
.field{position:absolute;background:#fff;height:34px;font-size:12px;color:#999;padding:9px 12px}
.footer .btn{left:626px;top:377px;width:100px;height:42px;line-height:42px;font-size:15px}
.info-row{left:780px;display:flex;gap:20px;align-items:center;font-size:14px;line-height:24px}
.info-row .ic{width:36px;height:36px;border-radius:50%;border:2px solid var(--teal);display:flex;align-items:center;justify-content:center;flex:none}
.social{left:780px;top:371px;display:flex;gap:10px}
.social i{width:32px;height:32px;border-radius:50%;background:#1f8fd8;display:block}
.social i:last-child{background:#d0243b}
.footer .rule{left:97px;top:456px;width:1006px;height:1px;background:#333}
.copy{top:492px;width:100%;text-align:center;font-size:14px;color:#ccc}
</style>
</head>
<body>

<header class="hero">
  <div class="brand abs"><span class="mark"></span>veltrin network</div>
  <nav class="nav abs">
    <a class="active" href="#">HOME</a><a href="#">WHAT IS VELTRIN</a><a href="#">SOURCE</a><a href="#">YELLOW PAPER</a><a href="#">CONTACT</a>
    <svg width="16" height="16" viewBox="0 0 16 16"><circle cx="6.5" cy="6.5" r="5" fill="none" stroke="#fff" stroke-width="2"/><path d="M10.5 10.5L15 15" stroke="#fff" stroke-width="2"/></svg>
  </nav>
  <h1 class="abs">VELTRIN NETWORK</h1>
  <p class="sub abs">We are a crypto currency company</p>
  <a class="btn abs" href="#">JOIN THE COMMUNITY</a>
  <svg class="play abs" width="44" height="44" viewBox="0 0 44 44"><circle cx="22" cy="22" r="21" fill="#fff"/><path d="M17 13l13 9-13 9z" fill="#1b1736"/></svg>
</header>

<section class="welcome">
  <h2 class="section-title abs">WELCOME TO VELTRIN NETWORK</h2>
  <p class="lead abs">Veltrin is a peer-to-peer graph to exchange and transact most crypto-currencies with NO fee or counterparty risk. Veltrin is a decentralized, and distributed ledger technology with built-in support to read across chains.</p>
  <div class="feature abs" style="left:89px">
    <div class="ring"><svg width="64" height="64" viewBox="0 0 64 64"><path d="M4 30L60 6 48 58 30 40z" fill="var(--teal)"/><path d="M30 40l-4 16 10-12" fill="var(--teal-dark)"/></svg></div>
    <h3>Receive Payments Faster</h3><p>At vero eos et accusamus et ius to odio dignissimos ducimus qui blanditis praesentium</p>
  </div>
  <div class="feature abs" style="left:349px">
    <div class="ring"><svg width="50" height="60" viewBox="0 0 50 60"><path d="M12 26V17a13 13 0 0 1 26 0v9" fill="none" stroke="var(--teal)" stroke-width="6"/><rect x="4" y="26" width="42" height="32" rx="3" fill="var(--teal)"/></svg></div>
    <h3>Blockchain Security</h3><p>At vero eos et accusamus et ius to odio dignissimos ducimus qui blanditis praesentium</p>
  </div>
  <div class="feature abs" style="left:611px">
    <div class="ring"><svg width="70" height="50" viewBox="0 0 70 50"><rect x="2" y="4" width="66" height="42" rx="3" fill="var(--teal)"/><rect x="8" y="10" width="54" height="30" fill="none" stroke="#fff" stroke-width="2"/><circle cx="35" cy="25" r="10" fill="#fff"/><circle cx="35" cy="25" r="5" fill="var(--teal)"/></svg></div>
    <h3>Low Commission Fees</h3><p>At vero eos et accusamus et ius to odio dignissimos ducimus qui blanditis praesentium</p>
  </div>
  <div class="feature abs" style="left:871px">
    <div class="ring"><svg width="56" height="56" viewBox="0 0 56 56" fill="var(--teal)"><path d="M2 2h18l-6 6 10 10-6 6-10-10-6 6zM54 2v18l-6-6-10 10-6-6 10-10-6-6zM2 54V36l6 6 10-10 6 6-10 10 6 6zM54 54H36l6-6-10-10 6-6 10 10 6-6z"/></svg></div>
    <h3>Highly redundant</h3><p>At vero eos et accusamus et ius to odio dignissimos ducimus qui blanditis praesentium</p>
  </div>
</section>

<section class="values">
  <div class="photo abs" role="img" aria-label="Gold coin glowing in a network of digital connections"></div>
  <div class="value-row abs">
    <svg width="62" height="56" viewBox="0 0 62 56"><rect x="20" y="2" width="22" height="12" rx="3" fill="none" stroke="#fff" stroke-width="4"/><rect x="2" y="12" width="58" height="42" rx="5" fill="#fff"/></svg>
    <div><h4>BUSINESS VALUE</h4><p>Legacy coins are expensive and slow to trade, in Veltrin Network coins can be traded or exchanged fast,.</p><span class="more">VIEW OUR ROADMAP</span></div>
  </div>
  <div class="value-row abs">
    <svg width="62" height="62" viewBox="0 0 62 62" fill="#fff"><ellipse cx="22" cy="10" rx="18" ry="7"/><rect x="4" y="16" width="36" height="9" rx="4"/><rect x="4" y="28" width="36" height="9" rx="4"/><rect x="4" y="40" width="36" height="9" rx="4"/><circle cx="46" cy="44" r="14"/></svg>
    <div><h4>COIN</h4><p>Legacy coins are expensive and slow to trade, in Veltrin Network coins can be traded or exchanged fast,.</p><span class="more">DOWNLOAD WALLET</span></div>
  </div>
  <div class="value-row abs">
    <svg width="62" height="62" viewBox="0 0 62 62"><path d="M18 28V19a13 13 0 0 1 26 0v9" fill="none" stroke="#fff" stroke-width="6"/><rect x="10" y="28" width="42" height="32" rx="3" fill="#fff"/></svg>
    <div><h4>DECENTRALIZED &amp; SECURE</h4><p>Legacy coins are expensive and slow to trade, in Veltrin Network coins can be traded or exchanged fast,.</p><span class="more">READ MORE</span></div>
  </div>
</section>

<section class="blog">
  <h2 class="section-title abs">LATEST BLOG</h2>
  <article class="post-main abs">
    <div class="img" role="img" aria-label="Trader at a laptop with stacked coins on the desk"></div>
    <h4>Finibus Bonorum et Malorum</h4>
    <div class="meta"><i></i>28/12/2017 &nbsp;|&nbsp; <i></i>John Doe</div>
    <p>Nam libero tempore, cum soluta nobis est eligendi optio cumque nihil impedit quo minus id quod maxime placat facere possimus, omnis voluptas voluptatibus maiores ali as consequ expedita distinct.</p>
    <span class="read">READ MORE</span>
  </article>
  <article class="post-item abs" style="top:175px">
    <div class="thumb" role="img" aria-label="Hand holding a card in warm light" style="background:linear-gradient(135deg,#1e2a3c,#c4622c)"></div>
    <h4>At vero eos et accusamus et iui</h4><div class="meta"><i></i>28/12/2017 &nbsp;|&nbsp; <i></i>John Doe</div>
    <p>Nam libero tempore, cum soluta nobis est eligendi optio cumque nihil impedit..</p>
  </article>
  <article class="post-item abs" style="top:318px">
    <div class="thumb" role="img" aria-label="Close-up of a blue circuit board" style="background:linear-gradient(135deg,#0f2b55,#2f6fb0)"></div>
    <h4>At vero eos et accusamus et iui</h4><div class="meta"><i></i>28/12/2017 &nbsp;|&nbsp; <i></i>John Doe</div>
    <p>Nam libero tempore, cum soluta nobis est eligendi optio cumque nihil impedit..</p>
  </article>
  <article class="post-item abs" style="top:461px">
    <div class="thumb" role="img" aria-label="Hand touching a glowing digital interface" style="background:linear-gradient(135deg,#34506e,#a9c3d8)"></div>
    <h4>At vero eos et accusamus et iui</h4><div class="meta"><i></i>28/12/2017 &nbsp;|&nbsp; <i></i>John Doe</div>
    <p>Nam libero tempore, cum soluta nobis est eligendi optio cumque nihil impedit..</p>
  </article>
  <a class="btn abs" href="#">VIEW ALL</a>
</section>

<section class="testimonials">
  <h2 class="section-title abs">TESTIMONIALS</h2>
  <div class="arrow abs" style="left:28px"><svg width="12" height="14"><path d="M10 1L3 7l7 6" fill="none" stroke="#fff" stroke-width="2.5"/></svg></div>
  <div class="quote abs" style="left:99px"><div class="avatar" role="img" aria-label="Portrait of Nora Felding"></div><p>Nam libero tempore, cum soluta nobis est eligendi optio cumque nihil impedit quo minus id quod maxime placea</p><h4>Nora Felding</h4></div>
  <div class="quote abs" style="left:447px"><div class="avatar" role="img" aria-label="Portrait of Celia Marsh"></div><p>Nam libero tempore, cum soluta nobis est eligendi optio cumque nihil impedit quo minus id quod maxime placea</p><h4>Celia Marsh</h4></div>
  <div class="quote abs" style="left:795px"><div class="avatar" role="img" aria-label="Portrait of Owen Tarrant"></div><p>Nam libero tempore, cum soluta nobis est eligendi optio cumque nihil impedit quo minus id quod maxime placea</p><h4>Owen Tarrant</h4></div>
  <div class="arrow abs" style="left:1132px"><svg width="12" height="14"><path d="M2 1l7 6-7 6" fill="none" stroke="#fff" stroke-width="2.5"/></svg></div>
</section>

<section class="partners">
  <h2 class="section-title abs">PARTNERS</h2>
  <svg class="abs" style="left:56px;top:230px" width="12" height="18"><path d="M10 1L2 9l8 8" fill="none" stroke="#555" stroke-width="2"/></svg>
  <div class="badge abs" style="left:99px;width:184px"><span></span></div>
  <div class="badge abs" style="left:304px;width:180px"><span></span></div>
  <div class="badge feature-badge abs" style="left:484px;width:232px"><span></span></div>
  <div class="badge abs" style="left:718px;width:180px"><span></span></div>
  <div class="badge abs" style="left:916px;width:186px"><span></span></div>
  <svg class="abs" style="left:1128px;top:230px" width="12" height="18"><path d="M2 1l8 8-8 8" fill="none" stroke="#555" stroke-width="2"/></svg>
</section>

<footer class="footer">
  <div class="to-top abs"><svg width="66" height="22"><path d="M0 22L33 0l33 22z" fill="#777"/></svg><div>TO TOP</div></div>
  <h3 class="abs" style="left:97px;top:118px">CONTACT FORM</h3>
  <div class="field" style="left:97px;top:201px;width:311px">Name</div>
  <div class="field" style="left:416px;top:201px;width:310px">Phone no.</div>
  <div class="field" style="left:97px;top:245px;width:629px">Email</div>
  <div class="field" style="left:97px;top:291px;width:629px;height:80px">Message</div>
  <a class="btn abs" href="#">SUBMIT</a>

  <h3 class="abs" style="left:780px;top:118px">CONTACT INFORMATION</h3>
  <div class="info-row abs" style="top:198px"><span class="ic"><svg width="12" height="16"><path d="M6 15S1 9 1 6a5 5 0 0 1 10 0c0 3-5 9-5 9z" fill="var(--teal)"/><circle cx="6" cy="6" r="2" fill="#111"/></svg></span><span>1820 Larkspur Avenue Suite 410<br>Fairview Colorado 80412</span></div>
  <div class="info-row abs" style="top:260px"><span class="ic"><svg width="14" height="14"><path d="M2 1h3l1.5 3.5L5 6a8 8 0 0 0 3 3l1.5-1.5L13 9v3a1 1 0 0 1-1 1A11 11 0 0 1 1 2a1 1 0 0 1 1-1z" fill="var(--teal)"/></svg></span><span>+1 555 014 2290</span></div>
  <div class="info-row abs" style="top:313px"><span class="ic"><svg width="14" height="11"><rect width="14" height="11" rx="1" fill="var(--teal)"/><path d="M1 1l6 5 6-5" fill="none" stroke="#111" stroke-width="1.3"/></svg></span><span>info@veltrinnet.org</span></div>
  <div class="social abs"><i></i><i></i><i></i><i></i></div>

  <div class="rule abs"></div>
  <p class="copy abs">Copyright © 2018, Veltrin Network. All rights reserved.</p>
</footer>

</body>
</html>
```